KRT Engineering Business Card Design

We’re looking for an elegant, clean, and timeless business card design that communicates experience, capability, and reliability.

KRT Engineering was established in 1995 , we are a Government Contracting company providing Professional Services to the Office of Frontier Affairs, Harbor Protection and the Vantage Collective. Our capabilities include: Acquisition & Program Management; Intelligence & Security Operations; Cyber, IT & Network Operations; Lifecycle Logistics & Asset Readiness; C5ISR Systems Engineering & Sustainment.

We want the card to reflect a straightforward, confident approach to business. The design should feel polished and professional without being flashy or overly corporate.

Design Direction
Clean, sophisticated, and uncluttered
Elegant but understated
Strong typography and thoughtful spacing
A timeless aesthetic rather than something overly trendy
Confident and established, with a sense of substance
Easy to read and practical in a real-world business setting

The overall impression should be: “These are experienced professionals who know what they’re doing, do what they say, and can be relied upon.”

We’re open to creative interpretations. The finished card should feel distinctive through its typography, proportions, layout, and attention to detail rather than through excessive graphics or visual effects.

We’re looking for a design that would make a potential client immediately feel that they’re dealing with a capable, trustworthy, and established company.

Company Colors: Navy and Gold/Yellow (but you do not need to use these colors on the card)
Company Name: KRT Engineering Associates, Inc. (known as KRT Engineering)
Website: krtengineering.com
Company Logo: Navy & Gold (other variations attached)

```html
<!DOCTYPE html>
<html lang="en">
<head>
<meta charset="utf-8">
<title>KRT Engineering Business Card</title>
<link href="https://fonts.googleapis.com/css2?family=Lato:wght@400;700;900&display=swap" rel="stylesheet">
<style>
  :root {
    --backdrop: #8e8e8e;
    --navy: #212a5e;
    --navy-deep: #1b2352;
    --gold: #fddf4a;
    --white: #ffffff;
    --shadow: rgba(0, 0, 0, 0.28);
  }
  * { margin: 0; padding: 0; box-sizing: border-box; }
  html, body {
    width: 1200px;
    height: 1000px;
    overflow: hidden;
    background: var(--backdrop);
    font-family: "Lato", Arial, sans-serif;
  }
  .card {
    position: absolute;
    left: 290px;
    width: 629px;
    height: 359px;
    border-radius: 23px;
    background: var(--navy);
    box-shadow: 0 3px 6px var(--shadow);
    overflow: hidden;
  }
  .card--front { top: 97px; }
  .card--back { top: 533px; }

  .wordmark {
    position: absolute;
    color: var(--white);
    font-weight: 900;
    letter-spacing: -1px;
    line-height: 1;
  }
  .card--front .wordmark {
    left: 83px;
    top: 158px;
    font-size: 52px;
  }

  .divider {
    position: absolute;
    left: 289px;
    top: 72px;
    width: 1.5px;
    height: 215px;
    background: var(--gold);
  }

  .details {
    position: absolute;
    left: 331px;
    top: 66px;
    color: var(--white);
  }
  .details__name {
    color: var(--gold);
    font-weight: 700;
    font-size: 27px;
    letter-spacing: 0.2px;
    line-height: 1.1;
  }
  .details__title {
    font-size: 16px;
    margin-top: 2px;
  }
  .details__company {
    color: var(--gold);
    font-weight: 700;
    font-size: 15px;
    margin-top: 14px;
  }
  .details__address {
    font-style: normal;
    font-size: 15px;
    line-height: 22px;
    margin-top: 2px;
    letter-spacing: 0.2px;
  }
  .contact-list {
    list-style: none;
    margin-top: 11px;
  }
  .contact-list li {
    display: flex;
    align-items: center;
    font-size: 15px;
    height: 21.5px;
    letter-spacing: 0.2px;
  }
  .contact-list svg {
    width: 12px;
    height: 12px;
    margin-right: 9px;
    flex: none;
  }

  .card__photo {
    position: absolute;
    inset: 0;
    background: radial-gradient(ellipse at 55% 45%, #1a2150 0%, #1c2455 45%, var(--navy-deep) 75%, var(--navy) 100%);
  }
  .card--back .wordmark {
    left: 0;
    right: 0;
    top: 140px;
    text-align: center;
    font-size: 88px;
  }
</style>
</head>
<body>
  <section class="card card--front">
    <div class="wordmark">KRT</div>
    <div class="divider"></div>
    <div class="details">
      <h1 class="details__name">MARLA QUENTIN</h1>
      <p class="details__title">President, CEO &amp; Founder</p>
      <p class="details__company">KRT Engineering Associates, Inc.</p>
      <address class="details__address">4820 Harlow Avenue, Suite 310<br>Brookport, VA 23190</address>
      <ul class="contact-list">
        <li>
          <svg viewBox="0 0 12 12" aria-hidden="true"><path fill="#fddf4a" d="M2.4 0.8l1.8 0 0.7 2.4-1.2 0.9c0.6 1.4 1.7 2.5 3.1 3.1l0.9-1.2 2.4 0.7 0 1.8c0 0.6-0.5 1.1-1.1 1.1C4.6 9.6 1.3 6.3 1.3 1.9c0-0.6 0.5-1.1 1.1-1.1z"/></svg>
          555-318-2040
        </li>
        <li>
          <svg viewBox="0 0 12 12" aria-hidden="true"><rect x="3" y="0.8" width="6" height="10.4" rx="1" fill="none" stroke="#fddf4a" stroke-width="1.4"/><rect x="5" y="8.6" width="2" height="1" fill="#fddf4a"/></svg>
          555-318-2040
        </li>
        <li>
          <svg viewBox="0 0 12 12" aria-hidden="true"><rect x="0.8" y="2.2" width="10.4" height="7.6" fill="#fddf4a"/><path d="M0.8 2.2l5.2 4 5.2-4" fill="none" stroke="#212a5e" stroke-width="1"/></svg>
          info@krtengineering.com
        </li>
        <li>
          <svg viewBox="0 0 12 12" aria-hidden="true"><circle cx="6" cy="6" r="5" fill="none" stroke="#fddf4a" stroke-width="1.3"/><path d="M6 1v10M1 6h10" stroke="#fddf4a" stroke-width="1"/></svg>
          krtengineering.com
        </li>
      </ul>
    </div>
  </section>

  <section class="card card--back">
    <div class="card__photo" role="img" aria-label="Faint navy-toned photograph of a military jet in flight"></div>
    <div class="wordmark">KRT</div>
  </section>
</body>
</html>
```